Business Card Design Project

I have established a company called "Corvella" which is a business specialising in psychotherapy/counselling , predominantly for anxiety & depression.

My name is Nel....hence, the Corvella link. However, Corvella was also chosen for its reference to green shoots of growth/recovery.

Corvella is to be "upmarket" and highly professional. I'm keen for the style and colours to reflect this.....taupe/grey with navy/black script, for example.....NO primary colours.

My name needs to be on the card and my mobile number. Not sure, but suspect it should also have my qualifications ( BA (Psych) & BSc (Hons) Psychology). Mobile number 0412 903 618.

```html
<!DOCTYPE html>
<html lang="en">
<head>
<meta charset="utf-8">
<title>Corvella – Business Card</title>
<link rel="stylesheet" href="https://fonts.googleapis.com/css2?family=Open+Sans:wght@400;600;700&family=Poiret+One&display=swap">
<style>
  :root {
    --page-bg: #ececec;
    --card-white: #ffffff;
    --brand-green: #8cc63f;
    --name-navy: #2b3157;
    --ink-black: #111111;
    --corner-light: #ffffff;
    --corner-grey: #4a4744;
    --band-light: #cfc6ba;
    --band-mid: #9a8d7e;
    --band-taupe: #5f5449;
    --swoosh-charcoal: #24272e;
    --swoosh-navy: #2b3157;
    --swoosh-slate: #6a6f80;
  }
  html, body {
    margin: 0;
    padding: 0;
    width: 1026px;
    height: 1200px;
    overflow: hidden;
    background: var(--page-bg);
  }
  .canvas {
    position: relative;
    width: 1026px;
    height: 1200px;
  }
  .card {
    position: absolute;
    left: 68px;
    top: 351px;
    width: 889px;
    height: 497px;
    background: var(--card-white);
    overflow: hidden;
  }
  .card-shapes {
    position: absolute;
    inset: 0;
    width: 100%;
    height: 100%;
  }
  .brand-name {
    position: absolute;
    left: 42px;
    top: 112px;
    margin: 0;
    font-family: "Open Sans", sans-serif;
    font-weight: 400;
    font-size: 60px;
    line-height: 1;
    color: var(--brand-green);
  }
  .practitioner {
    position: absolute;
    right: 168px;
    top: 84px;
    text-align: right;
    font-family: "Open Sans", sans-serif;
    color: var(--ink-black);
  }
  .practitioner-name {
    margin: 0 0 6px;
    font-family: "Poiret One", sans-serif;
    font-weight: 400;
    font-size: 96px;
    line-height: 1;
    color: var(--name-navy);
  }
  .qualifications {
    margin: 0;
    font-weight: 600;
    font-size: 28px;
    line-height: 38px;
  }
  .mobile {
    margin: 18px 0 0;
    font-weight: 600;
    font-size: 28px;
    line-height: 1;
  }
  .tagline {
    position: absolute;
    left: 56px;
    top: 402px;
    margin: 0;
    font-family: "Open Sans", sans-serif;
    font-weight: 400;
    font-size: 40px;
    line-height: 1;
    color: var(--card-white);
  }
</style>
</head>
<body>
<main class="canvas">
  <section class="card" aria-label="Corvella business card, front">
    <svg class="card-shapes" viewBox="0 0 254 142" preserveAspectRatio="none" aria-hidden="true">
      <defs>
        <linearGradient id="corner-fade" x1="0" y1="0" x2="1" y2="0">
          <stop offset="0" style="stop-color: var(--corner-light)"/>
          <stop offset="1" style="stop-color: var(--corner-grey)"/>
        </linearGradient>
        <linearGradient id="band-fade" x1="0" y1="0" x2="1" y2="0">
          <stop offset="0" style="stop-color: var(--band-light)"/>
          <stop offset="0.5" style="stop-color: var(--band-mid)"/>
          <stop offset="1" style="stop-color: var(--band-taupe)"/>
        </linearGradient>
        <linearGradient id="swoosh-fade" x1="0" y1="1" x2="1" y2="0">
          <stop offset="0" style="stop-color: var(--swoosh-charcoal)"/>
          <stop offset="0.5" style="stop-color: var(--swoosh-navy)"/>
          <stop offset="1" style="stop-color: var(--swoosh-slate)"/>
        </linearGradient>
      </defs>
      <path class="corner-curve" d="M206,0 Q244,26 250,72 L254,72 L254,0 Z" fill="url(#corner-fade)"/>
      <path class="taupe-band" d="M0,92 Q110,112 226,98 Q190,130 128,139 L0,142 Z" fill="url(#band-fade)"/>
      <path class="navy-swoosh" d="M132,142 Q232,124 254,56 L254,82 Q236,132 186,142 Z" fill="url(#swoosh-fade)"/>
    </svg>

    <p class="brand-name">Corvella</p>

    <div class="practitioner">
      <h1 class="practitioner-name">NEL</h1>
      <p class="qualifications">BA (Psych)<br>BSc (Hons) Psychology</p>
      <p class="mobile">Mobile: 0412 903 618</p>
    </div>

    <p class="tagline">specialising in psychotherapy</p>
  </section>
</main>
</body>
</html>
```